I need to make a car magnet

It needs to include the words "PLAVO TOUR" and "2026 MEMBER" as well as the attached silhouette of the golfer. The color scheme needs to be navy, red and white. The shape and dimensions are open for interpretation

```html
<!DOCTYPE html>
<html lang="en">
<head>
<meta charset="utf-8">
<title>PLAVO TOUR – 2026 Member Car Magnet</title>
<link rel="stylesheet" href="https://fonts.googleapis.com/css2?family=Russo+One&display=swap">
<style>
  :root {
    --backdrop: #b3b3b3;
    --white: #ffffff;
    --red: #e32232;
    --navy: #1e2a5c;
  }
  html, body {
    margin: 0;
    padding: 0;
    width: 892px;
    height: 1200px;
    overflow: hidden;
    background: var(--backdrop);
  }
  .canvas {
    position: relative;
    width: 892px;
    height: 1200px;
  }
  .car-magnet {
    position: absolute;
    left: 60px;
    top: 407px;
    width: 771px;
    height: 385px;
    background: var(--white);
    box-shadow: 1px 2px 4px rgba(0, 0, 0, 0.25);
  }
  .car-magnet svg {
    display: block;
    width: 100%;
    height: 100%;
  }
  .club-name {
    font-family: "Russo One", sans-serif;
    fill: var(--navy);
  }
  .member-line {
    font-family: "Russo One", sans-serif;
    fill: var(--red);
  }
</style>
</head>
<body>
<main class="canvas">
  <section class="car-magnet" aria-label="PLAVO TOUR 2026 member car magnet">
    <svg viewBox="0 0 771 385" xmlns="http://www.w3.org/2000/svg">
      <defs>
        <linearGradient id="base-band-fill" x1="0" y1="0" x2="1" y2="0">
          <stop offset="0.25" stop-color="var(--red)"/>
          <stop offset="0.75" stop-color="var(--navy)"/>
        </linearGradient>
      </defs>

      <rect class="base-band" role="img"
            aria-label="Decorative red-to-navy band along the bottom edge"
            x="0" y="300" width="771" height="85" fill="url(#base-band-fill)"/>

      <rect class="golfer-silhouette" role="img"
            aria-label="Navy silhouette of a golfer putting a ball toward the hole"
            x="36" y="27" width="179" height="334" rx="22" fill="var(--navy)"/>

      <text class="club-name" text-anchor="middle" font-size="90">
        <tspan x="500" y="108">PLAVO</tspan>
        <tspan x="500" y="202">TOUR</tspan>
      </text>
      <text class="member-line" x="500" y="254" font-size="30"
            text-anchor="middle">2026 MEMBER</text>
    </svg>
  </section>
</main>
</body>
</html>
```